Business Card for Fashion House

We need a business card design for our personalize fashion service for our customers. the business card should reflect reliability, luxury and creativity.
The brand Gravetto is extracted from "Graceful Velvetto"; Gravetto provides fashion designs sprinkled with luxury and style tailored for our elite clients character profile.
Gravetto is created for those who embody class and elegance with a passion for style.
Target Market(s)
Affluent Customers
Industry/Entity Type
Fashion
Contact Information for Business Card
Samira Haddadin
Fashion Designer
Telephone: +971 4 555 0192
Mobile +971 50 555 0147
Emal info@gravetto-example.com
Website www.gravetto-example.com
Social Media Youtube g+ Facebook Instagram Pin /gravetto
Font styles to use
Other font styles liked:
- Audrey provided
Look and feel
Each slider illustrates characteristics of the customer's brand and the style your logo design should communicate.

```html
<!DOCTYPE html>
<html lang="en">
<head>
<meta charset="utf-8">
<title>Gravetto — Business Card</title>
<link href="https://fonts.googleapis.com/css2?family=Cormorant+Garamond:wght@400&family=Open+Sans:wght@300;400&display=swap" rel="stylesheet">
<style>
  :root {
    --backdrop: #e8e6e3;
    --card: #1b1b1c;
    --card-edge: #a9abad;
    --ink: #bcbcbc;
    --ink-soft: #a3a3a3;
    --rule: #8f8f8f;
  }
  * { margin: 0; padding: 0; box-sizing: border-box; }
  html, body {
    width: 1200px;
    height: 900px;
    overflow: hidden;
    background: var(--backdrop);
  }
  .canvas {
    position: relative;
    width: 1200px;
    height: 900px;
  }
  .card {
    position: absolute;
    left: 320px;
    width: 560px;
    height: 320px;
    background: var(--card);
    border: 10px solid var(--card-edge);
    box-shadow: 0 10px 30px rgba(0,0,0,0.18);
  }
  .card--front { top: 100px; }
  .card--back { top: 480px; }

  .wordmark {
    font-family: "Cormorant Garamond", serif;
    font-weight: 400;
    color: var(--ink);
    text-transform: uppercase;
    letter-spacing: 0.42em;
  }

  /* Front */
  .front-brand {
    position: absolute;
    inset: 0;
    display: flex;
    flex-direction: column;
    align-items: center;
    justify-content: center;
    gap: 26px;
  }
  .front-brand .mark-dot {
    width: 46px;
    height: 46px;
    border: 3px solid var(--ink);
    border-radius: 50%;
  }
  .front-brand .wordmark {
    font-size: 34px;
    padding-left: 0.42em;
  }

  /* Back */
  .back-brand {
    position: absolute;
    left: 42px;
    top: 56px;
    font-size: 34px;
  }
  .holder {
    position: absolute;
    left: 44px;
    top: 130px;
    font-family: "Open Sans", sans-serif;
    color: var(--ink);
  }
  .holder__name {
    font-size: 17px;
    font-weight: 400;
    text-transform: uppercase;
    letter-spacing: 0.02em;
  }
  .holder__role {
    font-size: 13px;
    font-weight: 300;
    color: var(--ink-soft);
    margin-top: 2px;
  }
  .divider {
    position: absolute;
    left: 44px;
    right: 42px;
    top: 196px;
    height: 1px;
    background: var(--rule);
  }
  .contact {
    position: absolute;
    left: 44px;
    top: 212px;
    font-family: "Open Sans", sans-serif;
    font-weight: 300;
    font-size: 12.5px;
    line-height: 22px;
    color: var(--ink-soft);
    list-style: none;
  }
</style>
</head>
<body>
<main class="canvas">
  <section class="card card--front" aria-label="Card front">
    <div class="front-brand">
      <span class="mark-dot" aria-hidden="true"></span>
      <span class="wordmark">Gravetto</span>
    </div>
  </section>

  <section class="card card--back" aria-label="Card back">
    <div class="wordmark back-brand">Gravetto</div>
    <div class="holder">
      <p class="holder__name">Samira Haddadin</p>
      <p class="holder__role">Fashion Designer</p>
    </div>
    <div class="divider"></div>
    <ul class="contact">
      <li>Phn: +971 4 555 0192 | Cell: +971 50 555 0147</li>
      <li>Email: info@gravetto-example.com | www.gravetto-example.com</li>
    </ul>
  </section>
</main>
</body>
</html>
```